Exciting product design for natural pet treats

We need a design for our stand up doy style pouch that blends well with our current logo and also bold enough to stand out from the crowd.

We have a range of natural, Australian made pet treats and need a generic bag that allows for a sticker to be placed on the bag to idenfity the name, while also allowing a space for another sticker on the back for ingredients.
___
Information for the front is: logo, Australian made and owned, Pet Food Only (this is a small font and should not be hero text), 100% Natural, Visit our web site for more amazing products for your pets, Space for sticker 100 - 150mm x 30mm.
___
Information for the back is: Tailwag Depot is proudly Australian owned and operated. We source all our Tailwag Depot treats from reputable suppliers around Australia.

Our Tailwag Depot treats can be purchased through our online store, where you will find a growing range of other brands and products for your dogs, cats, birds, fish, rabbits, guinea pigs, horses, cows, sheep, chickens and more.

For further information, please visit our web site www.tailwagdepot.com.au or email us directly info@tailwagdepot.com.au.
____
The design will be used on three different bag sizes, so our printer can reduce the design from the largest size, but please keep in mind the sizes are 280mm x 380mm, 190mm x 275mm & 160mm x 230mm.

Target Market(s)

Mostly female, 25 to 65 years of age. Pet Lovers, particuarly focussing on dogs.

Industry/Entity Type

pet industry

Requirements
Must have
• Space for sticker on front for the product name 100mm x 30mm. Also a
Nice to have
• Space for a window.
Should not have
• comical pet images. Does not need an image of a pet. Does not need an image of the food.

```html
<!DOCTYPE html>
<html lang="en">
<head>
<meta charset="utf-8">
<title>Tailwag Depot – Treat Pouch, Front and Back</title>
<link rel="stylesheet" href="https://fonts.googleapis.com/css2?family=Oswald:wght@400;600&family=Josefin+Sans:wght@400;600&display=swap">
<style>
  :root {
    --bg: #e9e8e6;
    --pouch: #f4f4f5;
    --pouch-shade: #e2e2e5;
    --seal: #dadadd;
    --purple: #5a2d96;
    --violet: #7a3fc4;
    --navy: #241a52;
    --teal: #3ba6b3;
    --window: #7a5f3d;
    --window-light: #a4875c;
  }
  * { box-sizing: border-box; margin: 0; padding: 0; }
  html, body { width: 1200px; height: 798px; overflow: hidden; }
  body {
    background: var(--bg);
    font-family: "Oswald", "Arial Narrow", sans-serif;
    display: flex; align-items: center; justify-content: center; gap: 70px;
  }
  .pouch {
    position: relative;
    width: 400px; height: 620px;
    background: linear-gradient(100deg, var(--pouch-shade) 0%, var(--pouch) 30%, #fff 55%, var(--pouch) 80%, var(--pouch-shade) 100%);
    border-radius: 14px 14px 22px 22px;
    box-shadow: 0 10px 26px rgba(0,0,0,.12);
    display: flex; flex-direction: column; align-items: center;
    padding: 88px 36px 30px;
    text-align: center;
    overflow: hidden;
  }
  .pouch__seal {
    position: absolute; left: 0; right: 0; top: 0; height: 62px;
    background: linear-gradient(180deg, var(--seal), var(--pouch) 70%);
    border-bottom: 2px solid #d0d0d4;
  }
  .brand { display: flex; flex-direction: column; align-items: center; gap: 10px; }
  .brand__dot { width: 54px; height: 54px; border-radius: 50%; border: 3px solid var(--teal); }
  .brand__name { font-weight: 600; font-size: 40px; color: var(--navy); letter-spacing: .5px; line-height: 1; }
  .brand--row { flex-direction: row; gap: 12px; }
  .brand--row .brand__dot { width: 40px; height: 40px; }
  .brand--row .brand__name { font-size: 32px; }
  .tagline {
    font-family: "Josefin Sans", sans-serif; color: var(--violet);
    font-size: 15px; letter-spacing: 1px; margin-top: 8px;
  }
  .tagline--small { font-size: 10px; color: var(--teal); font-weight: 600; margin-top: 10px; }
  .sticker-space {
    width: 200px; height: 150px; margin-top: 16px;
    border: 2px dashed var(--purple); border-radius: 18px;
  }
  .sticker-space--ingredients { width: 240px; height: 200px; margin-top: 4px; }
  .label-small {
    font-family: "Josefin Sans", sans-serif; color: var(--teal);
    font-size: 9px; letter-spacing: .8px; margin-top: 12px;
  }
  .window-row { position: relative; margin-top: 14px; }
  .window {
    width: 220px; height: 170px; border-radius: 50%;
    background: radial-gradient(circle at 45% 40%, var(--window-light), var(--window) 70%);
  }
  .badge {
    position: absolute; right: -66px; top: 56px;
    font-size: 12px; font-weight: 600; color: var(--navy); line-height: 1.1;
  }
  .lead {
    color: var(--purple); font-weight: 600; text-transform: uppercase;
    font-size: 19px; line-height: 1.2; margin-top: 16px;
  }
  .lead--back { font-size: 20px; margin-top: 6px; }
  .url-pill {
    margin-top: 14px; padding: 7px 22px; border-radius: 20px;
    background: var(--teal); color: #fff; font-size: 14px; letter-spacing: .5px;
  }
  .body-copy {
    color: var(--purple); text-transform: uppercase;
    font-size: 13px; line-height: 1.35; margin-top: 18px;
  }
  .body-copy__head { color: var(--teal); font-size: 14px; margin-top: 14px; text-transform: uppercase; }
  .body-copy--contact { margin-top: 4px; }
</style>
</head>
<body>
  <section class="pouch pouch--front" aria-label="Pouch front">
    <div class="pouch__seal"></div>
    <div class="brand">
      <span class="brand__dot"></span>
      <span class="brand__name">Tailwag Depot</span>
    </div>
    <p class="tagline">PET FOOD ONLY</p>
    <div class="sticker-space" aria-label="Space for product name sticker"></div>
    <div class="window-row">
      <div class="window" role="img" aria-label="Clear window showing the treats inside"></div>
      <p class="badge">100%<br>NATURAL</p>
    </div>
    <p class="lead">Visit our web site for more<br>amazing products for your pets</p>
    <p class="url-pill">WWW.TAILWAGDEPOT.COM.AU</p>
  </section>

  <section class="pouch pouch--back" aria-label="Pouch back">
    <div class="pouch__seal"></div>
    <div class="brand brand--row">
      <span class="brand__dot"></span>
      <span class="brand__name">Tailwag Depot</span>
    </div>
    <p class="tagline tagline--small">PROUDLY AUSTRALIAN OWNED AND OPERATED</p>
    <p class="lead lead--back">We source all our Tailwag Depot treats from<br>reputable suppliers around Australia.</p>
    <p class="label-small">INGREDIENTS:</p>
    <div class="sticker-space sticker-space--ingredients" aria-label="Space for ingredients sticker"></div>
    <p class="body-copy">Our Tailwag Depot treats can be purchased through our online store, where you will find a growing range of other brands and products for your dogs, cats, birds, fish, rabbits, guinea pigs, horses, cows, sheep, chickens and more.</p>
    <p class="body-copy__head">For further information:</p>
    <p class="body-copy body-copy--contact">Please visit our web site www.tailwagdepot.com.au or<br>email us directly info@tailwagdepot.com.au.</p>
  </section>
</body>
</html>
```